Business Card Design for Flood Rescue 360 - Property Restoration Professionals

I need a business card designed for Flood Rescue 360. We are a full-service property restoration solution. Providing water, fire, smoke & storm restoration as well as mold remediation and full remodel or reconstruction to homes and businesses across Dallas-Fort Worth, TX.
Target Market(s)
home and business owners with insurance covered property damage from water, fire or storm related damage
Industry/Entity Type
property restoration
Contact Information for Business Card
Marcus Pelley General Manager Cell: 214-555-0193 Office: 469-555-0148 email: Marcus@FloodRescue360.example services: Water, Fire, Mold, Reconstruction Tagline: Urgency for Your Water Emergency!
Look and feel
Each slider illustrates characteristics of the customer's brand and the style your logo design should communicate.

```html
<!DOCTYPE html>
<html lang="en">
<head>
<meta charset="utf-8">
<title>Flood Rescue 360 – Business Card</title>
<link href="https://fonts.googleapis.com/css2?family=Montserrat:wght@400;600;700;800&display=swap" rel="stylesheet">
<style>
  :root {
    --brand-blue: #00b3e8;
    --brand-blue-light: #2cc3f0;
    --brand-blue-deep: #0098cc;
    --card-black: #1b1b1c;
    --text-white: #ffffff;
    --backdrop: #d9dadc;
  }
  * { margin: 0; padding: 0; box-sizing: border-box; }
  html, body { width: 1200px; height: 900px; overflow: hidden; }
  body {
    background: var(--backdrop);
    font-family: "Montserrat", sans-serif;
    position: relative;
  }
  .card {
    position: absolute;
    left: 250px;
    width: 700px;
    height: 400px;
    overflow: hidden;
    box-shadow: 0 10px 28px rgba(0,0,0,0.25);
  }

  /* Front */
  .card-front { top: 30px; background: var(--brand-blue); }
  .front-pattern {
    position: absolute; inset: 0;
    background: linear-gradient(120deg, var(--brand-blue-light) 0%, var(--brand-blue) 55%, var(--brand-blue-deep) 100%);
  }
  .front-brand {
    position: absolute; inset: 0;
    display: flex; align-items: center; justify-content: center;
  }
  .front-name {
    color: var(--text-white);
    font-weight: 700;
    font-size: 52px;
    line-height: 1;
    white-space: nowrap;
  }

  /* Back */
  .card-back { top: 470px; background: var(--card-black); color: var(--text-white); }
  .back-brand {
    position: absolute; right: 54px; top: 48px;
  }
  .back-name {
    color: var(--brand-blue);
    font-weight: 700;
    font-size: 34px;
    line-height: 1;
    white-space: nowrap;
  }
  .services {
    position: absolute; right: 54px; top: 170px;
    text-align: right;
  }
  .services-title {
    color: var(--brand-blue);
    font-weight: 800; font-size: 26px;
    letter-spacing: 0.5px; margin-bottom: 6px;
  }
  .services-list { list-style: none; font-size: 17px; font-weight: 400; line-height: 1.45; }
  .contact-block {
    position: absolute; left: 48px; bottom: 34px;
  }
  .name-row { display: flex; gap: 16px; margin-bottom: 20px; }
  .name-bar { width: 9px; background: var(--brand-blue); }
  .person-name {
    color: var(--brand-blue); font-weight: 800; font-size: 32px; line-height: 1.1;
  }
  .person-title { font-size: 18px; font-weight: 400; }
  .tagline { font-size: 18px; margin: 0 0 16px 25px; }
  .contact-list { list-style: none; margin-left: 25px; font-size: 17px; line-height: 1.5; }
  .contact-list li { display: flex; align-items: center; gap: 10px; }
  .contact-list svg { width: 16px; height: 16px; fill: var(--brand-blue); flex: none; }
</style>
</head>
<body>

  <section class="card card-front">
    <div class="front-pattern" role="img" aria-label="Repeating brand pattern in light and deep blue tones"></div>
    <div class="front-brand">
      <h1 class="front-name">Flood Rescue 360</h1>
    </div>
  </section>

  <section class="card card-back">
    <div class="back-brand">
      <h2 class="back-name">Flood Rescue 360</h2>
    </div>

    <div class="services">
      <h3 class="services-title">SERVICES</h3>
      <ul class="services-list">
        <li>Water</li>
        <li>Fire</li>
        <li>Mold</li>
        <li>Reconstruction</li>
      </ul>
    </div>

    <div class="contact-block">
      <div class="name-row">
        <span class="name-bar"></span>
        <div>
          <p class="person-name">Marcus Pelley</p>
          <p class="person-title">General Manager</p>
        </div>
      </div>
      <p class="tagline">Urgency for Your Water Emergency!</p>
      <ul class="contact-list">
        <li>
          <svg viewBox="0 0 16 16" aria-hidden="true"><path d="M4 0h8a1.5 1.5 0 0 1 1.5 1.5v13A1.5 1.5 0 0 1 12 16H4a1.5 1.5 0 0 1-1.5-1.5v-13A1.5 1.5 0 0 1 4 0zm0 2v10h8V2zm4 11a1 1 0 1 0 0 2 1 1 0 0 0 0-2z"/></svg>
          214-555-0193
        </li>
        <li>
          <svg viewBox="0 0 16 16" aria-hidden="true"><path d="M1 5c0-2 3-3 7-3s7 1 7 3v1.5h-3.5V5h-7v1.5H1zM4 7h8l2 7H2z"/></svg>
          469-555-0148
        </li>
        <li>
          <svg viewBox="0 0 16 16" aria-hidden="true"><path d="M1 3h14v10H1zm1.5 1.5v.3L8 9l5.5-4.2v-.3zM2.5 6.6v5h11v-5L8 10.8z"/></svg>
          Marcus@FloodRescue360.example
        </li>
        <li>
          <svg viewBox="0 0 16 16" aria-hidden="true"><circle cx="8" cy="8" r="7"/><path d="M1 8h14M8 1c3 3 3 11 0 14M8 1c-3 3-3 11 0 14" stroke="#1b1b1c" stroke-width="1" fill="none"/></svg>
          FloodRescue360.example
        </li>
      </ul>
    </div>
  </section>

</body>
</html>
```